Professional Package for CPA Firm

We would like a stationery design for our new CPA Firm based in Atlanta, GA called 'Vale 8'. We work with investors to help grow investments, tax free. We would like the design to have a professional/minimal look with a 'wow' factor. We need 9.5″ x 4.125″, 9x12, and 10x13 mailing envelopes, business cards, and a letterhead. We have a logo that is already complete. For the letterhead, we would like to have space to put credentials at the bottom of the page

Industry/Entity Type

CPA, Accounting

```html
<!DOCTYPE html>
<html lang="en">
<head>
<meta charset="utf-8">
<title>Vale 8 – Business Card</title>
<link rel="stylesheet" href="https://fonts.googleapis.com/css2?family=Lato:wght@400;700&family=Oswald:wght@500&display=swap">
<style>
  :root {
    --bg: #2a2b2d;
    --navy: #06253d;
    --teal: #1b8c98;
    --teal-bright: #23c3d6;
    --teal-deep: #0f6f7c;
    --red: #cf3a42;
    --paper: #f1f2f3;
    --white: #ffffff;
  }
  * { box-sizing: border-box; margin: 0; padding: 0; }
  html, body { width: 1200px; height: 874px; overflow: hidden; }
  body {
    background: var(--bg);
    font-family: "Lato", sans-serif;
    position: relative;
  }
  .card {
    position: absolute;
    left: 280px;
    width: 640px;
    height: 366px;
    overflow: hidden;
    box-shadow: 0 10px 30px rgba(0,0,0,.45);
  }
  .card--back { top: 51px; }
  .card--front { top: 457px; display: flex; }

  .back-pattern {
    position: absolute; inset: 0;
    background: linear-gradient(100deg, var(--teal-bright) 0%, var(--teal) 55%, var(--teal-deep) 100%);
  }
  .back-name {
    position: absolute;
    right: 36px; bottom: 30px;
    font-weight: 700;
    font-size: 22px;
    color: var(--white);
  }

  .contact-panel {
    width: 44%;
    background: var(--navy);
    padding: 58px 0 0 40px;
    color: var(--white);
  }
  .contact-name {
    font-family: "Oswald", sans-serif;
    font-weight: 500;
    font-size: 27px;
    color: var(--teal-bright);
    letter-spacing: .3px;
    line-height: 1;
  }
  .contact-title { font-size: 15px; margin-top: 4px; }
  .contact-address { font-size: 15px; line-height: 1.35; margin-top: 30px; }
  .contact-list { list-style: none; margin-top: 18px; font-size: 15px; line-height: 1.3; }
  .contact-list li { display: flex; align-items: center; gap: 10px; }
  .contact-list svg { width: 11px; height: 11px; fill: var(--teal-bright); flex: none; }

  .brand-panel {
    width: 56%;
    background: var(--paper);
    position: relative;
  }
  .brand-name {
    position: absolute;
    left: 40px; top: 86px;
    font-weight: 400;
    font-size: 44px;
    color: var(--navy);
    line-height: 1;
  }
  .brand-tagline {
    position: absolute;
    left: 42px; top: 146px;
    font-size: 15px;
    letter-spacing: 2.6px;
    color: var(--navy);
  }
  .brand-peaks {
    position: absolute;
    left: 0; right: 0; bottom: 0;
    height: 130px;
    background: linear-gradient(90deg, var(--navy) 0%, var(--teal) 50%, var(--red) 100%);
  }
</style>
</head>
<body>
  <section class="card card--back">
    <div class="back-pattern" role="img" aria-label="Teal repeating brand pattern"></div>
    <span class="back-name">Vale 8</span>
  </section>

  <section class="card card--front">
    <div class="contact-panel">
      <h1 class="contact-name">DANIEL HART</h1>
      <p class="contact-title">President</p>
      <p class="contact-address">214 Birchwood Court<br>Atlanta, Georgia 30309</p>
      <ul class="contact-list">
        <li><svg viewBox="0 0 24 24"><path d="M6.6 10.8a15.1 15.1 0 0 0 6.6 6.6l2.2-2.2c.3-.3.7-.4 1-.2 1.1.4 2.3.6 3.6.6.6 0 1 .4 1 1V20c0 .6-.4 1-1 1A17 17 0 0 1 3 4c0-.6.4-1 1-1h3.5c.6 0 1 .4 1 1 0 1.3.2 2.5.6 3.6.1.3 0 .7-.2 1z"/></svg>404-555-0182</li>
        <li><svg viewBox="0 0 24 24"><path d="M7 1h10a2 2 0 0 1 2 2v18a2 2 0 0 1-2 2H7a2 2 0 0 1-2-2V3a2 2 0 0 1 2-2zm0 3v14h10V4zm5 15.5a1.2 1.2 0 1 0 0 2.4 1.2 1.2 0 0 0 0-2.4z"/></svg>404-555-0147</li>
        <li><svg viewBox="0 0 24 24"><path d="M2 5h20v14H2zm2 2v.5l8 5 8-5V7zm0 2.8V17h16V9.8l-8 5z"/></svg>hello@vale8-cpa.com</li>
        <li><svg viewBox="0 0 24 24"><path d="M12 2a10 10 0 1 0 0 20 10 10 0 0 0 0-20zm0 2c1 0 2.3 2 2.8 5H9.2C9.7 6 11 4 12 4zM4.3 11h3.8c0 .7 0 1.4.1 2H4.3a8 8 0 0 1 0-2zm.6 4h3.6c.3 1.6.8 3 1.4 4A8 8 0 0 1 4.9 15zM9.2 15h5.6c-.5 3-1.8 5-2.8 5s-2.3-2-2.8-5zm6.3 4c.6-1 1.1-2.4 1.4-4h3.6a8 8 0 0 1-5 4zm.4-6c.1-.6.1-1.3.1-2h3.7a8 8 0 0 1 0 2z"/></svg>www.vale8-cpa.com</li>
      </ul>
    </div>
    <div class="brand-panel">
      <span class="brand-name">Vale 8</span>
      <span class="brand-tagline">CPAs and Tax Advisors</span>
      <div class="brand-peaks" role="img" aria-label="Brand peak shapes in navy, teal and red"></div>
    </div>
  </section>
</body>
</html>
```